Locksmith Business Cards

My father-in-law is in need of new business cards for his locksmith business and I need to impress him. Kindly help me out!

You can see the previous business card attached. It is a family run business in North Wales.

No individual names on the cards.

Key Things to Feature:
- The words "Prompt", "Local", "Reliable" (as you can see under the logo on the website)
- 24h Emergency Service
- Covering All of North Wales, the Wirral and Chester
- The color blue
- A key or a lock would be interesting (similar to the ones that come up when you google locksmith business card)

Optional (only if design includes bullet points, like the example below):
https://imgvaultcdn.net/samples/208314/55172/55172_3904821_208314_image.jpg
- Residential / Commercial / Automotive
- Alarms & Cameras
- Key Cutting & Safes

https://www.brynhafod-locksmiths.co.uk/

Industry/Entity Type

Locksmith

Contact Information for Business Card

01632 960 418
07700 900 362
brynhafodlocksmiths@mailvane.com
Brynhafod Locksmiths, The Willow Barn, 7 Tannery Rd., Llandudno LL99 4QX
www.brynhafod-locksmiths.co.uk

Requirements
Must have
• - The words "Prompt", "Local", "Reliable" (as you can see under the logo on the website)
• - 24h Emergency Service
• - Covering All of North Wales, the Wirral and Chester
Nice to have
• - A key or a lock would be interesting (similar to the ones that come up when you google locksmith business card)

```html
<!DOCTYPE html>
<html lang="en">
<head>
<meta charset="utf-8">
<title>Brynhafod Locksmiths – Business Card</title>
<link rel="stylesheet" href="https://fonts.googleapis.com/css2?family=Oswald:wght@500&family=Source+Sans+3:wght@400;500&display=swap">
<style>
  :root {
    --navy: #1c2662;
    --brand-blue: #3f4f9a;
    --card-grey: #b5bcbc;
    --paper: #ffffff;
    --ink: #1d1d1f;
    --rule: #9a9a9a;
    --stage: #e4e5e6;
  }
  * { margin: 0; padding: 0; box-sizing: border-box; }
  html, body {
    width: 1200px; height: 802px; overflow: hidden;
    background: var(--stage);
    font-family: "Source Sans 3", "Myriad Pro", sans-serif;
    color: var(--ink);
  }
  .canvas { position: relative; width: 1200px; height: 802px; }
  .card {
    position: absolute; top: 274px; width: 442px; height: 265px;
    box-shadow: 0 3px 8px rgba(0,0,0,0.25);
    overflow: hidden;
  }
  /* Contact side */
  .card--contact { left: 136px; background: var(--card-grey); }
  .card__panel {
    position: absolute; left: 0; top: 0; width: 205px; height: 265px;
    background: var(--navy);
  }
  .contact-block {
    position: absolute; right: 26px; text-align: right;
    font-size: 12.6px; line-height: 15.8px;
  }
  .contact-block--address { top: 60px; }
  .contact-block--reach { top: 116px; }
  .contact-block--service { top: 193px; }
  .contact-line { display: flex; justify-content: flex-end; align-items: center; gap: 2px; }
  .contact-line svg { width: 10px; height: 10px; fill: var(--navy); flex: none; }
  .contact-rule {
    position: absolute; left: 219px; top: 185px; width: 197px; height: 1px;
    background: var(--navy);
  }
  /* Brand side */
  .card--brand { left: 624px; background: var(--paper); }
  .brand-mark {
    position: absolute; left: 121px; top: 76px;
    display: flex; align-items: center; gap: 10px;
  }
  .brand-mark__square { width: 46px; height: 46px; background: var(--navy); border-radius: 4px; }
  .brand-mark__name {
    font-weight: 500; font-size: 29px; line-height: 29px;
    color: var(--brand-blue); text-transform: uppercase; letter-spacing: 0.2px;
  }
  .tagline {
    position: absolute; left: 0; right: 0; top: 148px;
    padding-left: 50px; text-align: center;
    font-family: "Oswald", "Arial Narrow", sans-serif; font-weight: 500;
    font-size: 13.5px; color: var(--navy);
  }
  .brand-rule {
    position: absolute; left: 108px; top: 188px; width: 227px; height: 1px;
    background: var(--rule);
  }
  .services {
    position: absolute; left: 0; right: 0; top: 200px; text-align: center;
    font-size: 12.6px; line-height: 15.8px;
  }
  .services__dot {
    display: inline-block; width: 6px; height: 6px; border-radius: 50%;
    background: var(--navy); margin: 0 7px; vertical-align: middle;
  }
</style>
</head>
<body>
<main class="canvas">
  <section class="card card--contact" aria-label="Contact side">
    <div class="card__panel"></div>
    <div class="contact-block contact-block--address">
      <p>Brynhafod Locksmiths</p>
      <p>The Willow Barn, 7 Tannery</p>
      <p>Rd., Llandudno LL99 4QX</p>
    </div>
    <div class="contact-block contact-block--reach">
      <p class="contact-line">01632 960 418
        <svg viewBox="0 0 10 10" aria-hidden="true"><path d="M1 3.5C1 2 2.5 1.5 5 1.5S9 2 9 3.5L7.5 4 7 3H3L2.5 4zM2.5 5h5l1 3.5h-7z"/></svg></p>
      <p class="contact-line">07700 900 362
        <svg viewBox="0 0 10 10" aria-hidden="true"><path d="M3 0.5h4v9H3zM3.8 1.5v6h2.4v-6z"/></svg></p>
      <p class="contact-line">brynhafodlocksmiths@mailvane.com
        <svg viewBox="0 0 10 10" aria-hidden="true"><path d="M0.5 2h9v6h-9zM1.2 2.6 5 5.6 8.8 2.6z" fill-rule="evenodd"/></svg></p>
      <p class="contact-line">www.brynhafod-locksmiths.co.uk
        <svg viewBox="0 0 10 10" aria-hidden="true"><circle cx="5" cy="5" r="4.5"/></svg></p>
    </div>
    <div class="contact-rule"></div>
    <div class="contact-block contact-block--service">
      <p>24h Emergency Service</p>
      <p>Covering All of North Wales,</p>
      <p>the Wirral and Chester</p>
    </div>
  </section>

  <section class="card card--brand" aria-label="Brand side">
    <div class="brand-mark">
      <span class="brand-mark__square"></span>
      <span class="brand-mark__name">Brynhafod<br>Locksmiths</span>
    </div>
    <p class="tagline">Prompt. Local. Reliable</p>
    <div class="brand-rule"></div>
    <div class="services">
      <p>Residential / Commercial / Automotive</p>
      <p>Alarms &amp; Cameras<span class="services__dot"></span>Key Cutting &amp; Safes</p>
    </div>
  </section>
</main>
</body>
</html>
```